University Social app needs Instagram layout help - tile layout and designs for 18 different types

We need a instagram profile look for our app Tindleloop that is getting a new look and feel. We want 18 different tiles designs that mesh well and look good together on the profile page. This can be a mix of images and text. Tindleloop is based in Sydney, Australia and is a Social app that helps students connect IRL ,find new friends and activities/experiences through society campus events. Topics can include but not limited to the following: Whats on, society spotlight, how to use Tindleloop, Tindleloop features, memes, Helpful hits, POV, Uni Life IRL, Make the Connection, Try Something New, Tindleloop Community, Student Voice, Uni 101, Tindleloop It, Student Stories. please also see current Tindleloop instagram page for content type ideas. It also needs to have the new Tindleloop brand colours (#04ccd9 with a gradient to white background) (also see attached file). The final tiles should communicate university fun, connection and a place to find events. Swap out the current stickers for activity based stickers similar to the attached examples to demonstrate that the app is for finding fun events and activities and for connection.
Look and feel
Each slider illustrates characteristics of the customer's brand and the style your logo design should communicate.

```html
<!DOCTYPE html>
<html lang="en">
<head>
<meta charset="utf-8">
<title>Tindleloop tile set</title>
<link href="https://fonts.googleapis.com/css2?family=Montserrat:wght@800&family=Poppins:wght@600&family=Quicksand:wght@500&display=swap" rel="stylesheet">
<style>
  :root {
    --brand-cyan: #04ccd9;
    --tile-cyan: #8ee9ef;
    --ink: #0a0a0a;
    --paper: #ffffff;
    --sun: #ffe000;
    --backdrop: #e8e6e5;
    --dot: #3a3f6a;
  }
  * { margin: 0; padding: 0; box-sizing: border-box; }
  html, body { width: 1200px; height: 799px; overflow: hidden; }
  body { background: var(--backdrop); position: relative; font-family: "Poppins", sans-serif; color: var(--ink); }

  .tile { position: absolute; overflow: hidden; box-shadow: 0 1px 2px rgba(0,0,0,.12); }
  .tile--cyan { background: var(--tile-cyan); }
  .tile--white { background: var(--paper); }
  .abs { position: absolute; }

  .dot-grid { position: absolute; }
  .wordmark { position: absolute; font-family: "Poppins", sans-serif; font-weight: 600; color: var(--ink); white-space: nowrap; }
  .display { font-family: "Montserrat", sans-serif; font-weight: 800; color: var(--ink); }

  /* Find events tile */
  .find-events { left: 145px; top: 108px; width: 271px; height: 271px; }
  .find-events .corner-disc { right: -55px; top: -55px; width: 110px; height: 110px; border-radius: 50%; background: var(--paper); }
  .find-events .headline { position: absolute; left: 77px; top: 42px; font-size: 27px; line-height: 25px; letter-spacing: .2px; }
  .find-events .highlight { position: absolute; left: 59px; top: 148px; width: 150px; height: 52px; }
  .find-events .wordmark { left: 93px; top: 219px; font-size: 19px; }
  .find-events .half-disc { left: 15px; bottom: -19px; width: 38px; height: 38px; border-radius: 50%; background: var(--ink); }

  /* Community tile */
  .community { left: 145px; top: 426px; width: 272px; height: 271px; }
  .community .half-disc { left: 207px; top: -20px; width: 40px; height: 40px; border-radius: 50%; background: var(--ink); }
  .community .people-icon { left: 100px; top: 44px; }
  .community .title { position: absolute; left: 0; right: 0; top: 96px; text-align: center; font-size: 24px; }
  .community .swoosh { left: 62px; top: 124px; }
  .community .blurb { position: absolute; left: 36px; right: 36px; top: 158px; font-family: "Quicksand", sans-serif; font-size: 6.6px; line-height: 7.7px; text-align: center; }
  .community .wordmark { left: 0; right: 0; top: 219px; text-align: center; font-size: 19px; }
  .community .side-block { left: 0; top: 125px; width: 18px; height: 36px; background: var(--brand-cyan); }
  .community .pill { right: 0; top: 228px; width: 40px; height: 15px; border-radius: 8px 0 0 8px; background: var(--ink); }

  /* Whats on tile */
  .whats-on { left: 777px; top: 106px; width: 274px; height: 274px; }
  .whats-on .corner-block { left: 0; top: 0; width: 41px; height: 44px; background: var(--brand-cyan); }
  .whats-on .pill { left: 231px; top: 0; width: 16px; height: 41px; border-radius: 0 0 8px 8px; background: var(--ink); }
  .whats-on .calendar { left: 119px; top: 52px; }
  .whats-on .title { position: absolute; left: 0; right: 0; top: 98px; text-align: center; font-size: 26px; padding-left: 6px; }
  .whats-on .swoosh { left: 70px; top: 129px; }
  .whats-on .tagline { position: absolute; left: 0; right: 0; top: 149px; text-align: center; font-family: "Quicksand", sans-serif; font-size: 17px; line-height: 20px; }
  .whats-on .arrow { left: 115px; top: 200px; }
  .whats-on .half-disc { left: 68px; top: 218px; width: 40px; height: 40px; border-radius: 50%; background: var(--ink); clip-path: inset(0 50% 0 0); }
  .whats-on .foot-block { left: 180px; top: 256px; width: 36px; height: 18px; background: var(--brand-cyan); }

  /* Helpful hits tile */
  .helpful-hits { left: 778px; top: 425px; width: 273px; height: 272px; }
  .helpful-hits .half-disc { left: 4px; top: -20px; width: 40px; height: 40px; border-radius: 50%; background: var(--ink); }
  .helpful-hits .title { position: absolute; left: 45px; top: 37px; font-size: 29px; }
  .helpful-hits .swoosh { left: 38px; top: 70px; }
  .helpful-hits .rule { left: 33px; width: 208px; height: 1.4px; background: var(--ink); }
  .helpful-hits .pill { right: 0; top: 231px; width: 41px; height: 16px; border-radius: 8px 0 0 8px; background: var(--ink); }
  .helpful-hits .foot-block { left: 33px; top: 255px; width: 36px; height: 17px; background: var(--sun); }

  /* Photo post tile */
  .photo-post { left: 463px; top: 262px; width: 274px; height: 274px; }
  .photo-post .photo { position: absolute; inset: 0; background:
      radial-gradient(ellipse 60% 30% at 50% 62%, rgba(40,44,46,.45), transparent 70%),
      linear-gradient(180deg, #f1fcfd 0%, #c8f1f4 18%, #a9b6b8 40%, #7d8587 60%, #5c6264 80%, #474c4e 100%); }
  .photo-post .half-disc { left: -20px; top: 16px; width: 40px; height: 40px; border-radius: 50%; background: var(--ink); }
  .photo-post .wordmark { left: 162px; top: 23px; font-size: 18px; }
  .photo-post .burst { left: 0; top: 0; }
</style>
</head>
<body>

<!-- Find events tile -->
<section class="tile tile--cyan find-events">
  <div class="abs corner-disc"></div>
  <svg class="highlight" viewBox="0 0 150 52" aria-hidden="true">
    <path d="M6 6 L146 3 L143 24 L148 27 L140 49 L10 50 L14 30 L2 28 Z" fill="var(--sun)"/>
  </svg>
  <h1 class="display headline">Find<br>events,<br>join<br>societies<br>make new<br>friends</h1>
  <svg class="dot-grid" style="left:19px;top:233px" width="32" height="32" aria-hidden="true">
    <g fill="var(--dot)"><circle cx="2" cy="2" r="0.9"/><circle cx="11" cy="2" r="0.9"/><circle cx="20" cy="2" r="0.9"/><circle cx="29" cy="2" r="0.9"/><circle cx="2" cy="11" r="0.9"/><circle cx="11" cy="11" r="0.9"/><circle cx="20" cy="11" r="0.9"/><circle cx="29" cy="11" r="0.9"/><circle cx="2" cy="20" r="0.9"/><circle cx="11" cy="20" r="0.9"/><circle cx="20" cy="20" r="0.9"/><circle cx="29" cy="20" r="0.9"/><circle cx="2" cy="29" r="0.9"/><circle cx="11" cy="29" r="0.9"/><circle cx="20" cy="29" r="0.9"/><circle cx="29" cy="29" r="0.9"/></g>
  </svg>
  <span class="wordmark">Tindleloop</span>
  <div class="abs half-disc"></div>
</section>

<!-- Community tile -->
<section class="tile tile--white community">
  <div class="abs half-disc"></div>
  <svg class="dot-grid" style="left:212px;top:28px" width="32" height="32" aria-hidden="true">
    <g fill="var(--dot)"><circle cx="2" cy="2" r="0.9"/><circle cx="11" cy="2" r="0.9"/><circle cx="20" cy="2" r="0.9"/><circle cx="29" cy="2" r="0.9"/><circle cx="2" cy="11" r="0.9"/><circle cx="11" cy="11" r="0.9"/><circle cx="20" cy="11" r="0.9"/><circle cx="29" cy="11" r="0.9"/><circle cx="2" cy="20" r="0.9"/><circle cx="11" cy="20" r="0.9"/><circle cx="20" cy="20" r="0.9"/><circle cx="29" cy="20" r="0.9"/><circle cx="2" cy="29" r="0.9"/><circle cx="11" cy="29" r="0.9"/><circle cx="20" cy="29" r="0.9"/><circle cx="29" cy="29" r="0.9"/></g>
  </svg>
  <svg class="abs people-icon" width="74" height="44" viewBox="0 0 74 44" aria-hidden="true">
    <g stroke="var(--ink)" stroke-width="4" fill="none" stroke-linejoin="round">
      <path d="M3 41 C3 28 9 22 15 22 C21 22 27 28 27 41 Z" fill="var(--brand-cyan)"/>
      <path d="M47 41 C47 28 53 22 59 22 C65 22 71 28 71 41 Z" fill="var(--brand-cyan)"/>
      <path d="M24 41 C24 26 30 20 37 20 C44 20 50 26 50 41 Z" fill="var(--paper)"/>
      <circle cx="15" cy="12" r="7" fill="var(--paper)"/>
      <circle cx="59" cy="12" r="7" fill="var(--paper)"/>
      <circle cx="37" cy="9" r="7" fill="var(--paper)"/>
    </g>
  </svg>
  <h2 class="display title">Community</h2>
  <svg class="abs swoosh" width="150" height="8" viewBox="0 0 150 8" aria-hidden="true">
    <path d="M2 6 C50 2 100 1 148 3" stroke="var(--brand-cyan)" stroke-width="3.5" fill="none" stroke-linecap="round"/>
  </svg>
  <p class="blurb">Meet students who share your interests, join society events on campus, swap tips about uni life and find people to explore the city with. Every week brings new faces, fresh plans and more reasons to get out there.</p>
  <span class="wordmark">Tindleloop</span>
  <div class="abs side-block"></div>
  <div class="abs pill"></div>
</section>

<!-- Photo post tile -->
<section class="tile photo-post">
  <div class="photo" role="img" aria-label="Photo of a group of students sitting together on the grass by the harbour, toned grey with a cyan-to-white fade at the top"></div>
  <svg class="abs burst" width="274" height="274" viewBox="0 0 274 274" aria-hidden="true">
    <g stroke="var(--sun)" stroke-width="3" stroke-linecap="round" fill="none">
      <path d="M39 107 L41 122"/>
      <path d="M61 105 L55 119"/>
      <path d="M21 121 L32 130"/>
      <path d="M200 115 L196 129"/>
      <path d="M227 128 L209 136"/>
      <path d="M216 152 L232 154"/>
    </g>
  </svg>
  <div class="abs half-disc"></div>
  <svg class="dot-grid" style="left:30px;top:22px" width="32" height="30" aria-hidden="true">
    <g fill="var(--dot)"><circle cx="2" cy="2" r="0.9"/><circle cx="11" cy="2" r="0.9"/><circle cx="20" cy="2" r="0.9"/><circle cx="29" cy="2" r="0.9"/><circle cx="2" cy="11" r="0.9"/><circle cx="11" cy="11" r="0.9"/><circle cx="20" cy="11" r="0.9"/><circle cx="29" cy="11" r="0.9"/><circle cx="2" cy="20" r="0.9"/><circle cx="11" cy="20" r="0.9"/><circle cx="20" cy="20" r="0.9"/><circle cx="29" cy="20" r="0.9"/><circle cx="2" cy="29" r="0.9"/><circle cx="11" cy="29" r="0.9"/><circle cx="20" cy="29" r="0.9"/><circle cx="29" cy="29" r="0.9"/></g>
  </svg>
  <span class="wordmark">Tindleloop</span>
</section>

<!-- Whats on tile -->
<section class="tile tile--white whats-on">
  <div class="abs corner-block"></div>
  <div class="abs pill"></div>
  <svg class="abs calendar" width="44" height="40" viewBox="0 0 44 40" aria-hidden="true">
    <rect x="2" y="6" width="40" height="32" rx="6" fill="none" stroke="var(--ink)" stroke-width="3"/>
    <line x1="2" y1="15" x2="42" y2="15" stroke="var(--ink)" stroke-width="3"/>
    <line x1="12" y1="1" x2="12" y2="10" stroke="var(--ink)" stroke-width="3" stroke-linecap="round"/>
    <line x1="32" y1="1" x2="32" y2="10" stroke="var(--ink)" stroke-width="3" stroke-linecap="round"/>
    <g fill="var(--brand-cyan)">
      <rect x="8" y="20" width="5" height="4"/><rect x="16" y="20" width="5" height="4"/><rect x="24" y="20" width="5" height="4"/><rect x="32" y="20" width="5" height="4"/>
      <rect x="8" y="28" width="5" height="4"/><rect x="16" y="28" width="5" height="4"/><rect x="24" y="28" width="5" height="4"/><rect x="32" y="28" width="5" height="4"/>
    </g>
  </svg>
  <h2 class="display title">Whats On?</h2>
  <svg class="abs swoosh" width="140" height="10" viewBox="0 0 140 10" aria-hidden="true">
    <path d="M3 8 C45 3 95 2 137 2" stroke="var(--brand-cyan)" stroke-width="3.5" fill="none" stroke-linecap="round"/>
  </svg>
  <p class="tagline">Find the best<br>events near you</p>
  <svg class="abs arrow" width="46" height="16" viewBox="0 0 46 16" aria-hidden="true">
    <path d="M2 9 L42 8 M33 2 L43 8 L34 14" stroke="var(--brand-cyan)" stroke-width="2.6" fill="none" stroke-linecap="round" stroke-linejoin="round"/>
  </svg>
  <svg class="dot-grid" style="left:25px;top:223px" width="32" height="32" aria-hidden="true">
    <g fill="var(--dot)"><circle cx="2" cy="2" r="0.9"/><circle cx="11" cy="2" r="0.9"/><circle cx="20" cy="2" r="0.9"/><circle cx="29" cy="2" r="0.9"/><circle cx="2" cy="11" r="0.9"/><circle cx="11" cy="11" r="0.9"/><circle cx="20" cy="11" r="0.9"/><circle cx="29" cy="11" r="0.9"/><circle cx="2" cy="20" r="0.9"/><circle cx="11" cy="20" r="0.9"/><circle cx="20" cy="20" r="0.9"/><circle cx="29" cy="20" r="0.9"/><circle cx="2" cy="29" r="0.9"/><circle cx="11" cy="29" r="0.9"/><circle cx="20" cy="29" r="0.9"/><circle cx="29" cy="29" r="0.9"/></g>
  </svg>
  <div class="abs half-disc"></div>
  <div class="abs foot-block"></div>
</section>

<!-- Helpful hits tile -->
<section class="tile tile--cyan helpful-hits">
  <div class="abs half-disc"></div>
  <svg class="dot-grid" style="left:12px;top:30px" width="32" height="32" aria-hidden="true">
    <g fill="var(--dot)"><circle cx="2" cy="2" r="0.9"/><circle cx="11" cy="2" r="0.9"/><circle cx="20" cy="2" r="0.9"/><circle cx="29" cy="2" r="0.9"/><circle cx="2" cy="11" r="0.9"/><circle cx="11" cy="11" r="0.9"/><circle cx="20" cy="11" r="0.9"/><circle cx="29" cy="11" r="0.9"/><circle cx="2" cy="20" r="0.9"/><circle cx="11" cy="20" r="0.9"/><circle cx="20" cy="20" r="0.9"/><circle cx="29" cy="20" r="0.9"/><circle cx="2" cy="29" r="0.9"/><circle cx="11" cy="29" r="0.9"/><circle cx="20" cy="29" r="0.9"/><circle cx="29" cy="29" r="0.9"/></g>
  </svg>
  <h2 class="display title">Helpful Hits</h2>
  <svg class="abs swoosh" width="196" height="10" viewBox="0 0 196 10" aria-hidden="true">
    <path d="M3 8 C60 4 130 3 193 4" stroke="var(--paper)" stroke-width="3.5" fill="none" stroke-linecap="round"/>
  </svg>
  <div class="abs rule" style="top:111px"></div>
  <div class="abs rule" style="top:132px"></div>
  <div class="abs rule" style="top:152px"></div>
  <div class="abs rule" style="top:174px"></div>
  <div class="abs rule" style="top:195px"></div>
  <div class="abs rule" style="top:216px"></div>
  <div class="abs pill"></div>
  <div class="abs foot-block"></div>
</section>

</body>
</html>
```